LHP Regal Business Card Design 2020

Your Manor Steward is looking for a business card that is clean and straight to the point but still looks high-end and attractive. We are a team comprised of management and field professionals focused on the high-end residential marketplace. We serve homeowners and trade professionals directly based out of the Metrowest/Alder area. We provide client services as well as construction/renovation services.
We are aiming for a black and white feel (white background and black text) and a matte finish with rounded edges.

We want to emphasis our vision of "Estates - Upgrades - Alliances".
Dana Pellham is the president of LHP

Please include the following areas we service: Alder/Cove/Harbor
Please make sure to include Dana's mobile (555) 213 4480 & office number (555) 640 1937, email dana@yourmanorsteward.example and website www.yourmanorsteward.example

Colors

Designer to choose only greyscale colors for use in the design.

Requirements
Must have
• Include "Estates - Upgrades - Alliances" in design

Include "After Hours Emergency Support # 1800 555 0142" with icon

```html
<!DOCTYPE html>
<html lang="en">
<head>
<meta charset="utf-8">
<title>LHP Business Cards</title>
<link href="https://fonts.googleapis.com/css2?family=Montserrat:wght@700;800&family=Source+Sans+3:wght@400;600&display=swap" rel="stylesheet">
<style>
  :root {
    --page: #e3e6e6;
    --card: #ffffff;
    --ink: #222526;
    --band: #1f2223;
    --band-light: #5e6061;
    --band-text: #d9dbdb;
    --front-bg: #222425;
    --front-mark: #3a3d3e;
    --front-text: #c9cbcb;
  }
  * { margin: 0; padding: 0; box-sizing: border-box; }
  html, body { width: 801px; height: 1200px; overflow: hidden; background: var(--page); }
  body { position: relative; font-family: "Source Sans 3", "Myriad Pro", sans-serif; color: var(--ink); }

  .card {
    position: absolute; width: 338px; height: 193px;
    background: var(--card); border-radius: 12px; overflow: hidden;
    box-shadow: 2px 3px 5px rgba(0,0,0,.28);
  }
  .col-a { left: 41px; } .col-b { left: 422px; }
  .row-1 { top: 55px; } .row-2 { top: 278px; } .row-3 { top: 499px; } .row-4 { top: 725px; } .row-5 { top: 951px; }

  .brand { position: absolute; left: 21px; top: 22px; }
  .brand-mark { font-family: "Montserrat", sans-serif; font-weight: 800; font-size: 40px; line-height: 1; color: var(--ink); letter-spacing: -1px; }
  .brand-name { font-family: "Montserrat", sans-serif; font-weight: 700; font-size: 7px; letter-spacing: .09em; margin-top: 7px; padding-left: 3px; }
  .brand.centered { left: 0; right: 0; top: 24px; text-align: center; }
  .brand.centered .brand-mark { font-size: 48px; }
  .brand.centered .brand-name { font-size: 8.5px; margin-top: 6px; }

  .person { position: absolute; right: 21px; top: 83px; text-align: right; }
  .person-name { font-family: "Montserrat", sans-serif; font-weight: 700; font-size: 12.5px; line-height: 1.1; }
  .person-role { font-size: 9px; line-height: 1.3; }

  .rule { position: absolute; left: 21px; right: 21px; top: 113px; height: 1px; background: var(--ink); }

  .contacts { position: absolute; left: 21px; top: 120px; list-style: none; font-size: 9px; line-height: 11.3px; }
  .contacts li { display: flex; align-items: center; gap: 3px; }
  .contacts svg { width: 9px; height: 9px; flex: none; fill: var(--ink); }

  .areas { position: absolute; right: 21px; top: 154px; font-size: 9px; line-height: 11.3px; word-spacing: 2px; }

  .band { position: absolute; left: 0; right: 0; bottom: 0; height: 19px;
    background: linear-gradient(90deg, var(--band) 0 78%, var(--band-light) 92%); }
  .band-site { position: absolute; left: 21px; top: 3px; font-size: 9px; letter-spacing: .1em; color: var(--band-text); }
  .band-mark { position: absolute; right: 21px; top: 0; font-family: "Montserrat", sans-serif; font-weight: 800; font-size: 15px; line-height: 19px; color: #fff; }

  .card.front { background: var(--front-bg); }
  .front-mark { position: absolute; left: 0; right: 0; top: 56px; text-align: center;
    font-family: "Montserrat", sans-serif; font-weight: 800; font-size: 70px; line-height: 1; color: var(--front-mark); letter-spacing: -2px; }
  .front-tagline { position: absolute; left: 0; right: 0; top: 167px; text-align: center;
    font-size: 9px; letter-spacing: .16em; color: var(--front-text); }
</style>
</head>
<body>
<svg width="0" height="0" style="position:absolute" aria-hidden="true">
  <symbol id="i-mobile" viewBox="0 0 10 10"><path d="M3 0h4a1 1 0 0 1 1 1v8a1 1 0 0 1-1 1H3a1 1 0 0 1-1-1V1a1 1 0 0 1 1-1zm0 1.2v6.6h4V1.2z"/></symbol>
  <symbol id="i-phone" viewBox="0 0 10 10"><path d="M2 .5l1.8 2-1 1.2a6 6 0 0 0 3.5 3.5l1.2-1 2 1.8-1.2 1.5C4.5 9.3.7 5.5.5 1.7z"/></symbol>
  <symbol id="i-alarm" viewBox="0 0 10 10"><path d="M3 4.5a2 2 0 0 1 4 0V8H3zM1.8 8.3h6.4V10H1.8zM4.7 0h.6v1.6h-.6zM1 1.2l.5-.4 1 1.2-.5.4zm8 0-.5-.4-1 1.2.5.4zM0 4h1.5v.6H0zm8.5 0H10v.6H8.5z"/></symbol>
  <symbol id="i-mail" viewBox="0 0 10 10"><path d="M0 2h10v6.5H0zm1 1v.3l4 2.6 4-2.6V3zm0 1.5v3h8v-3l-4 2.6z"/></symbol>
</svg>

<div class="card front col-a row-1">
  <div class="front-mark">LHP</div>
  <div class="front-tagline">ESTATES - UPGRADES - ALLIANCES</div>
</div>

<div class="card col-b row-1">
  <div class="brand"><div class="brand-mark">LHP</div><div class="brand-name">YOUR MANOR STEWARD</div></div>
  <div class="person"><div class="person-name">DANA PELLHAM</div><div class="person-role">President</div></div>
  <div class="rule"></div>
  <ul class="contacts">
    <li><svg><use href="#i-mobile"/></svg>(555) 213 4480</li>
    <li><svg><use href="#i-phone"/></svg>(555) 640 1937</li>
    <li><svg><use href="#i-alarm"/></svg>(800) 555 0142</li>
    <li><svg><use href="#i-mail"/></svg>dana@yourmanorsteward.example</li>
  </ul>
  <div class="areas">ALDER | COVE | HARBOR</div>
  <div class="band"><span class="band-site">yourmanorsteward.example</span><span class="band-mark">LHP</span></div>
</div>

<div class="card col-a row-2">
  <div class="brand"><div class="brand-mark">LHP</div><div class="brand-name">YOUR MANOR STEWARD</div></div>
  <div class="person"><div class="person-name">OWEN MARSH</div><div class="person-role">Vice President</div></div>
  <div class="rule"></div>
  <ul class="contacts">
    <li><svg><use href="#i-mobile"/></svg>(555) 213 4480</li>
    <li><svg><use href="#i-phone"/></svg>(555) 640 1937</li>
    <li><svg><use href="#i-alarm"/></svg>(800) 555 0142</li>
    <li><svg><use href="#i-mail"/></svg>dana@yourmanorsteward.example</li>
  </ul>
  <div class="areas">ALDER | COVE | HARBOR</div>
  <div class="band"><span class="band-site">yourmanorsteward.example</span><span class="band-mark">LHP</span></div>
</div>

<div class="card col-b row-2">
  <div class="brand"><div class="brand-mark">LHP</div><div class="brand-name">YOUR MANOR STEWARD</div></div>
  <div class="person"><div class="person-name">LEO BRANDT</div><div class="person-role">Client Services</div></div>
  <div class="rule"></div>
  <ul class="contacts">
    <li><svg><use href="#i-mobile"/></svg>(555) 213 4480</li>
    <li><svg><use href="#i-phone"/></svg>(555) 640 1937</li>
    <li><svg><use href="#i-alarm"/></svg>(800) 555 0142</li>
    <li><svg><use href="#i-mail"/></svg>dana@yourmanorsteward.example</li>
  </ul>
  <div class="areas">ALDER | COVE | HARBOR</div>
  <div class="band"><span class="band-site">yourmanorsteward.example</span><span class="band-mark">LHP</span></div>
</div>

<div class="card col-a row-3">
  <div class="brand"><div class="brand-mark">LHP</div><div class="brand-name">YOUR MANOR STEWARD</div></div>
  <div class="person"><div class="person-name">EVAN CORLEY</div><div class="person-role">Project Supervisor</div></div>
  <div class="rule"></div>
  <ul class="contacts">
    <li><svg><use href="#i-mobile"/></svg>(555) 213 4480</li>
    <li><svg><use href="#i-phone"/></svg>(555) 640 1937</li>
    <li><svg><use href="#i-alarm"/></svg>(800) 555 0142</li>
    <li><svg><use href="#i-mail"/></svg>dana@yourmanorsteward.example</li>
  </ul>
  <div class="areas">ALDER | COVE | HARBOR</div>
  <div class="band"><span class="band-site">yourmanorsteward.example</span><span class="band-mark">LHP</span></div>
</div>

<div class="card col-b row-3">
  <div class="brand"><div class="brand-mark">LHP</div><div class="brand-name">YOUR MANOR STEWARD</div></div>
  <div class="person"><div class="person-name">MILES DUNN</div><div class="person-role">Project Supervisor</div></div>
  <div class="rule"></div>
  <ul class="contacts">
    <li><svg><use href="#i-mobile"/></svg>(555) 213 4480</li>
    <li><svg><use href="#i-phone"/></svg>(555) 640 1937</li>
    <li><svg><use href="#i-alarm"/></svg>(800) 555 0142</li>
    <li><svg><use href="#i-mail"/></svg>dana@yourmanorsteward.example</li>
  </ul>
  <div class="areas">ALDER | COVE | HARBOR</div>
  <div class="band"><span class="band-site">yourmanorsteward.example</span><span class="band-mark">LHP</span></div>
</div>

<div class="card col-a row-4">
  <div class="brand"><div class="brand-mark">LHP</div><div class="brand-name">YOUR MANOR STEWARD</div></div>
  <div class="person"><div class="person-name">CLARA VENTURI</div><div class="person-role">Client Services</div></div>
  <div class="rule"></div>
  <ul class="contacts">
    <li><svg><use href="#i-mobile"/></svg>(555) 213 4480</li>
    <li><svg><use href="#i-phone"/></svg>(555) 640 1937</li>
    <li><svg><use href="#i-alarm"/></svg>(800) 555 0142</li>
    <li><svg><use href="#i-mail"/></svg>dana@yourmanorsteward.example</li>
  </ul>
  <div class="areas">ALDER | COVE | HARBOR</div>
  <div class="band"><span class="band-site">yourmanorsteward.example</span><span class="band-mark">LHP</span></div>
</div>

<div class="card col-b row-4">
  <div class="brand"><div class="brand-mark">LHP</div><div class="brand-name">YOUR MANOR STEWARD</div></div>
  <div class="person"><div class="person-name">PAUL ASHBY</div><div class="person-role">Field Supervisor</div></div>
  <div class="rule"></div>
  <ul class="contacts">
    <li><svg><use href="#i-mobile"/></svg>(555) 213 4480</li>
    <li><svg><use href="#i-phone"/></svg>(555) 640 1937</li>
    <li><svg><use href="#i-alarm"/></svg>(800) 555 0142</li>
    <li><svg><use href="#i-mail"/></svg>dana@yourmanorsteward.example</li>
  </ul>
  <div class="areas">ALDER | COVE | HARBOR</div>
  <div class="band"><span class="band-site">yourmanorsteward.example</span><span class="band-mark">LHP</span></div>
</div>

<div class="card col-a row-5">
  <div class="brand"><div class="brand-mark">LHP</div><div class="brand-name">YOUR MANOR STEWARD</div></div>
  <div class="person"><div class="person-name">GUS MORRELL</div><div class="person-role">Lead Field Service Technician</div></div>
  <div class="rule"></div>
  <ul class="contacts">
    <li><svg><use href="#i-mobile"/></svg>(555) 213 4480</li>
    <li><svg><use href="#i-phone"/></svg>(555) 640 1937</li>
    <li><svg><use href="#i-alarm"/></svg>(800) 555 0142</li>
    <li><svg><use href="#i-mail"/></svg>dana@yourmanorsteward.example</li>
  </ul>
  <div class="areas">ALDER | COVE | HARBOR</div>
  <div class="band"><span class="band-site">yourmanorsteward.example</span><span class="band-mark">LHP</span></div>
</div>

<div class="card col-b row-5">
  <div class="brand centered"><div class="brand-mark">LHP</div><div class="brand-name">YOUR MANOR STEWARD</div></div>
  <div class="rule"></div>
  <ul class="contacts">
    <li><svg><use href="#i-mobile"/></svg>(555) 213 4480</li>
    <li><svg><use href="#i-phone"/></svg>(555) 640 1937</li>
    <li><svg><use href="#i-alarm"/></svg>(800) 555 0142</li>
    <li><svg><use href="#i-mail"/></svg>dana@yourmanorsteward.example</li>
  </ul>
  <div class="areas">ALDER | COVE | HARBOR</div>
  <div class="band"><span class="band-site">yourmanorsteward.example</span><span class="band-mark">LHP</span></div>
</div>
</body>
</html>
```